Heritage Hollow Business Cards

Require a business card design. <br/><br/>Needs to include logo (either round or long version) plus these details:<br/>Maya Torvell<br/>Heritage Hollow<br/>maya@kelvadtrading.com.au<br/>02 6481 7395<br/>PO Box Glenwarra NSW 2791<br/>www.heritagehollow.com.au<br/><br/>I need in an editable format so that I can create for multiple staff members. <br/><br/>

Target Market(s)

We are an online store selling renovation products to home owners are builders. Looking for a classic classy design.

Industry/Entity Type

Home And Garden

Contact Information for Business Card

Maya Torvell
Heritage Hollow
maya@kelvadtrading.com.au
02 6481 7395
PO Box Glenwarra NSW 2791
www.heritagehollow.com.au

Colors

Designer to choose colors to be used in the design.

Requirements
Must have
• Must include Logo.

```html
<!DOCTYPE html>
<html lang="en">
<head>
<meta charset="utf-8">
<title>Heritage Hollow Business Cards</title>
<link href="https://fonts.googleapis.com/css2?family=Work+Sans:wght@400;500;600&display=swap" rel="stylesheet">
<style>
  :root {
    --backdrop: #dcdcdc;
    --card-dark: #1c1c1c;
    --card-light: #ffffff;
    --ink: #1f1f1f;
    --ink-soft: #6a6a6a;
    --ink-mid: #4a4a4a;
    --on-dark: #f2f2f2;
    --accent-bar: #222222;
  }
  * { box-sizing: border-box; margin: 0; padding: 0; }
  html, body {
    width: 1200px; height: 900px; overflow: hidden;
    background: var(--backdrop);
    font-family: "Work Sans", Arial, sans-serif;
  }
  .sheet {
    width: 1200px; height: 900px;
    display: flex; flex-direction: column;
    align-items: center; justify-content: center; gap: 36px;
  }
  .card {
    width: 660px; height: 400px; position: relative;
    box-shadow: 0 6px 18px rgba(0,0,0,0.18);
  }
  .card--front {
    background: radial-gradient(ellipse at 60% 40%, #2a2a2a 0%, var(--card-dark) 70%);
    color: var(--on-dark);
  }
  .card--back { background: var(--card-light); color: var(--ink); }

  .brand { display: flex; align-items: center; gap: 14px; }
  .brand__dot {
    width: 22px; height: 22px; border-radius: 50%;
    border: 2px solid currentColor;
  }
  .brand__name { font-weight: 500; font-size: 34px; letter-spacing: 0.5px; }

  .card--front .brand {
    position: absolute; left: 0; right: 0; top: 150px; justify-content: center;
  }
  .front__web {
    position: absolute; left: 0; right: 0; top: 312px;
    text-align: center; font-size: 15px; letter-spacing: 4px;
  }

  .back__bar {
    position: absolute; left: 0; top: 52px; width: 18px; height: 48px;
    background: var(--accent-bar);
  }
  .back__details { position: absolute; left: 54px; top: 50px; }
  .person__name { font-weight: 600; font-size: 30px; letter-spacing: 1.5px; line-height: 1.1; }
  .person__role { font-size: 15px; color: var(--ink-soft); margin-top: 2px; letter-spacing: 0.5px; }
  .company { font-size: 17px; color: var(--ink); margin-top: 22px; margin-left: 8px; }
  .address { font-size: 17px; color: var(--ink-soft); margin-top: 6px; line-height: 1.35; letter-spacing: 0.5px; }
  .contacts { list-style: none; margin-top: 28px; }
  .contacts li {
    display: flex; align-items: center; gap: 12px;
    font-size: 17px; color: var(--ink-mid); line-height: 1.55; letter-spacing: 0.3px;
  }
  .contacts svg { width: 14px; height: 14px; flex: none; }
  .card--back .brand {
    position: absolute; right: 50px; top: 128px; color: var(--ink);
  }
  .card--back .brand__name { font-size: 28px; }
</style>
</head>
<body>
<main class="sheet">
  <section class="card card--front" aria-label="Card front">
    <div class="brand">
      <span class="brand__dot"></span>
      <span class="brand__name">Heritage Hollow</span>
    </div>
    <p class="front__web">www.heritagehollow.com.au</p>
  </section>

  <section class="card card--back" aria-label="Card back">
    <span class="back__bar"></span>
    <div class="back__details">
      <h1 class="person__name">Maya Torvell</h1>
      <p class="person__role">Director</p>
      <p class="company">Heritage Hollow</p>
      <p class="address">PO Box Glenwarra<br>NSW 2791</p>
      <ul class="contacts">
        <li>
          <svg viewBox="0 0 16 16" aria-hidden="true"><path d="M4 1.5c.6 0 1.5 2.6 1.5 3.2S4.4 6 4.6 6.7c.5 1.6 2.4 3.8 4 4.5.6.3 1.3-1 1.9-1s3 1.1 3 1.7-1.4 2.6-2.6 2.6C6.4 14.5 1.5 8.7 1.5 4.4 1.5 2.8 3.4 1.5 4 1.5z" fill="#333"/></svg>
          02 6481 7395
        </li>
        <li>
          <svg viewBox="0 0 16 16" aria-hidden="true"><rect x="1.5" y="3.5" width="13" height="9" fill="none" stroke="#333" stroke-width="1.4"/><path d="M1.5 3.5 8 9l6.5-5.5" fill="none" stroke="#333" stroke-width="1.4"/></svg>
          maya@kelvadtrading.com.au
        </li>
        <li>
          <svg viewBox="0 0 16 16" aria-hidden="true"><circle cx="8" cy="8" r="6.5" fill="none" stroke="#333" stroke-width="1.3"/><ellipse cx="8" cy="8" rx="2.8" ry="6.5" fill="none" stroke="#333" stroke-width="1.1"/><path d="M1.5 8h13M2.5 5h11M2.5 11h11" stroke="#333" stroke-width="1"/></svg>
          www.heritagehollow.com.au
        </li>
      </ul>
    </div>
    <div class="brand">
      <span class="brand__dot"></span>
      <span class="brand__name">Heritage Hollow</span>
    </div>
  </section>
</main>
</body>
</html>
```